Quick Straightforward Billboard Redesign

- Design billboard sized for 10 foot' x 36' foot width live area size and please include bleeds 6" around all sides
- Exact blue color match is imperative in headline, logo, phone number bubble or wherever used. C-83 / M-45 / Y-1 / K-0-
- What I hope to illustrate is that our company offers the best porch screening in the area area, in regards to quality, expertise, durability, storms proof, but we do not build screen porches.
- Current board is attached below from previous designer, and as you can see sizing was off, white space on edges make it appear to be sized incorrectly.
- I also attached my own little mock up idea well well if it helps, favorite image, logo, headline, etc and ideas perhaps on expanding or making this better?

Thanks so much!

Target Market(s)

Drivers and passengers, Southeastern NC, are of immense new construction and high end homes.

Industry/Entity Type

Construction

Colors
0054AA
0677BA
7BADD7
CADEEF
E8F1F8

Requirements
Must have
• Blue color matching
Nice to have
• Design spins or other thoughts on my little mock up

```html
<!DOCTYPE html>
<html lang="en">
<head>
<meta charset="utf-8">
<title>Harborline Screens – Billboard</title>
<link rel="stylesheet" href="https://fonts.googleapis.com/css2?family=Anton&display=swap">
<style>
  :root {
    --brand-blue: #0063ae;
    --brand-green: #00b65e;
    --cream: #f2eee5;
    --white: #ffffff;
    --backdrop: #787f88;
  }
  * { margin: 0; padding: 0; box-sizing: border-box; }
  html, body { width: 1145px; height: 1200px; overflow: hidden; }
  body { background: var(--backdrop); position: relative; font-family: "Anton", "Arial Narrow", sans-serif; }

  .billboard {
    position: absolute; left: 40px; top: 440px; width: 1065px; height: 320px;
    background: var(--white); overflow: hidden;
    box-shadow: 0 6px 14px rgba(0,0,0,.35);
  }
  .billboard__photo {
    position: absolute; left: 0; top: 0; width: 365px; height: 100%;
    background: linear-gradient(180deg, #eef0f1 0%, #e3e6e8 22%, #8cb7e0 30%, #7d9f62 42%, #7a6a58 60%, #6e6150 76%, #cfc8bb 100%);
  }
  .billboard__headline {
    position: absolute; left: 393px; top: 22px;
    font-size: 78px; line-height: 1; color: var(--brand-blue); letter-spacing: -0.5px;
    white-space: nowrap;
  }
  .billboard__band {
    position: absolute; left: 355px; top: 110px; right: 0; height: 81px;
    background: var(--brand-green);
  }
  .billboard__tagline {
    position: absolute; left: 38px; top: 8px;
    font-size: 64px; line-height: 1; color: var(--white); white-space: nowrap;
  }
  .brand {
    position: absolute; left: 392px; top: 222px; display: flex; align-items: center; gap: 12px;
  }
  .brand__square { width: 56px; height: 56px; background: var(--brand-blue); }
  .brand__name {
    font-size: 31px; line-height: 1.12; color: var(--brand-blue); text-transform: uppercase;
  }
  .phone-pill {
    position: absolute; left: 663px; top: 213px; right: 0; height: 79px;
    background: var(--brand-blue); border-radius: 16px 0 0 16px;
    display: flex; align-items: center; padding-left: 16px; gap: 12px;
    box-shadow: 0 8px 10px -6px rgba(0,0,0,.35);
  }
  .phone-pill__icon { width: 44px; height: 44px; flex: none; }
  .phone-pill__number { font-size: 56px; line-height: 1; color: var(--cream); white-space: nowrap; }
</style>
</head>
<body>
  <section class="billboard">
    <div class="billboard__photo" role="img" aria-label="Photo of a screened coastal porch with wicker lounge chairs, ceiling fan and a lake view"></div>
    <h1 class="billboard__headline">Screen your Porch.</h1>
    <div class="billboard__band">
      <p class="billboard__tagline">BUILT FOR THE COAST.</p>
    </div>
    <div class="brand">
      <span class="brand__square"></span>
      <p class="brand__name">Harborline<br>Screens</p>
    </div>
    <div class="phone-pill">
      <svg class="phone-pill__icon" viewBox="0 0 44 44" aria-hidden="true">
        <circle cx="22" cy="22" r="21" fill="#ffffff"/>
        <circle cx="22" cy="22" r="18" fill="var(--brand-green)"/>
        <path d="M15 13c1-1 2.5-1 3.2 0l2 3c.6.9.3 2-.5 2.6l-1.2.9c1 2.5 3 4.5 5.5 5.5l.9-1.2c.6-.8 1.7-1.1 2.6-.5l3 2c1 .7 1 2.2 0 3.2l-1.3 1.3c-1.2 1.2-3 1.5-4.6.8C19.5 28.4 15.6 24.5 13.4 19.4c-.7-1.6-.4-3.4.8-4.6z" fill="#ffffff"/>
      </svg>
      <span class="phone-pill__number">555.014.0199</span>
    </div>
  </section>
</body>
</html>
```